Award-winnning Estate Agent needs a premium version of their 'For Sale' board design

We need a premium option for our 'For Sale' board design. We have a standard board that is attached to this brief, but were are looking to have a premium design version that we will use when selling exclusive properties. Our company name is Harbourline Vale Estates and the name for this is exclusive selection is: 'The Harbourline Collection'. The design needs to work with our current brand, but have a distinctive PREMIUM feel to it. I have uploaded the barnd guidelines and also some of the exisisting logo variations. We do NOT need a new logo but feel free to play around with colours, fonts, sizes etc. for the sign.

Target Market(s)

Property buyers & house hunters

Industry/Entity Type

Real Estate - Residential Property

Font styles to use
Sans Serif

Requirements
Must have
• A premium fee, must be square design, must be easy to read when driving past the sign
Nice to have
• I'm open ot ideas

```html
<!DOCTYPE html>
<html lang="en">
<head>
<meta charset="utf-8">
<title>Harbourline Vale Estates – For Sale Board</title>
<link href="https://fonts.googleapis.com/css2?family=Tinos:wght@400;700&display=swap" rel="stylesheet">
<style>
  :root {
    --board: #e7e7e7;
    --gold: #c4a265;
    --gold-pale: #e6d9c0;
    --ink: #0b0b0b;
    --paper: #ffffff;
    --backdrop: #f4f4f2;
  }
  html, body {
    margin: 0;
    width: 1200px;
    height: 1199px;
    overflow: hidden;
    background: var(--backdrop);
    font-family: "Tinos", "Times New Roman", serif;
  }
  .board {
    position: relative;
    width: 1200px;
    height: 1199px;
    background: var(--board);
    overflow: hidden;
  }
  .board-shapes { position: absolute; inset: 0; }
  .collection-title {
    position: absolute; top: 150px; left: 0; width: 100%;
    text-align: center; margin: 0;
    color: var(--gold); font-size: 40px; font-weight: 700;
    letter-spacing: 1px; text-transform: uppercase;
  }
  .headline {
    position: absolute; top: 190px; left: 0; width: 100%;
    text-align: center; margin: 0;
    color: var(--ink); font-size: 156px; font-weight: 700;
    line-height: 1; letter-spacing: 2px;
  }
  .agency-name {
    position: absolute; top: 470px; left: 0; width: 100%;
    text-align: center; margin: 0;
    color: var(--ink); font-size: 76px; font-weight: 700;
    line-height: 1.1; letter-spacing: 3px; text-transform: uppercase;
  }
  .contact {
    position: absolute; left: 110px; width: 985px; text-align: center;
    color: var(--paper); font-weight: 700; margin: 0;
  }
  .contact-phone { top: 930px; font-size: 104px; line-height: 1; }
  .contact-web { top: 1085px; font-size: 62px; line-height: 1; }
</style>
</head>
<body>
  <main class="board">
    <svg class="board-shapes" width="1200" height="1199" viewBox="0 0 1200 1199" aria-hidden="true">
      <!-- roof band -->
      <rect x="0" y="0" width="1200" height="260" fill="var(--gold)"/>
      <polygon points="0,195 610,0 1200,255 1200,1199 0,1199" fill="var(--board)"/>
      <!-- side rails -->
      <rect x="14" y="240" width="14" height="959" fill="var(--gold-pale)"/>
      <rect x="1172" y="240" width="14" height="959" fill="var(--gold-pale)"/>
      <!-- agency mark circle -->
      <circle cx="600" cy="560" r="0" fill="none"/>
      <!-- contact house shape -->
      <polygon points="110,1000 610,818 1095,1000 1095,1199 110,1199" fill="var(--ink)"/>
      <line x1="110" y1="1060" x2="1095" y2="1052" stroke="var(--gold)" stroke-width="4"/>
      <!-- phone badge -->
      <circle cx="610" cy="806" r="42" fill="var(--gold)" stroke="var(--paper)" stroke-width="5"/>
      <path d="M594 788 q-6 4 -2 14 q8 16 22 24 q9 5 14 -1 l3 -4 l-10 -8 l-5 5 q-10 -5 -15 -15 l5 -5 l-8 -10 z" fill="var(--paper)"/>
    </svg>

    <p class="collection-title">The Harbourline Collection</p>
    <h1 class="headline">FOR SALE</h1>
    <p class="agency-name">Harbourline Vale<br>Estates</p>

    <p class="contact contact-phone">01632 960418</p>
    <p class="contact contact-web">harbourlinevaleestates.co.uk</p>
  </main>
</body>
</html>
```